One page front and back healthcare law brochure

Our small law firm provides legal services to businesses in the health care industry. We would like a single page 8.5x11 front and back brochure that highlights the services we offer. The intent of the brochure is to communicate our professionalism, high work quality, and depth of experience in healthcare law.
Target Market(s)
Doctors, Hospitals, Medical practices, Dental practices, Healthcare clinics, Healthcare tech companies, Healthcare entrepreneurs, Nurses, Med Spas, Pain Management Clinics, Weight Loss Clinics
Industry/Entity Type
Legal, Healthcare
Requirements
Nice to have
- Visually align with https://vennory.law/ and https://vennory.law/health-care/

```html
<!DOCTYPE html>
<html lang="en">
<head>
<meta charset="utf-8">
<title>Vennory Law Healthcare Law Brochure</title>
<link href="https://fonts.googleapis.com/css2?family=Montserrat:wght@700&family=Poppins:wght@300;400;500;600&display=swap" rel="stylesheet">
<style>
:root{
  --backdrop:#b3b3b3;
  --navy:#0556a8;
  --brand:#0b57a6;
  --sky:#1c8fd2;
  --ink:#111;
  --body:#444;
  --paper:#fff;
  --photo-a:#c9ced6;
  --photo-b:#5b6b85;
}
*{margin:0;padding:0;box-sizing:border-box}
html,body{width:1200px;height:793px;overflow:hidden;background:var(--backdrop)}
.stage{position:relative;width:1200px;height:793px;overflow:hidden;font-family:'Poppins',sans-serif;color:var(--ink)}
.backdrop{position:absolute;inset:0}
.page{position:absolute;top:61px;width:518px;height:670px;background:var(--paper);box-shadow:0 2px 8px rgba(0,0,0,.18);overflow:hidden}
.page--front{left:57px}
.page--back{left:625px}
.firm-name{position:absolute;top:11px;left:0;right:0;text-align:center;font-family:'Poppins',sans-serif;font-weight:500;font-size:12px;line-height:14px;color:var(--brand)}
.photo{position:absolute;background:linear-gradient(135deg,var(--photo-a),var(--photo-b))}
.photo--team{left:0;top:36px;width:518px;height:286px;border-radius:10px}
.photo--staff{left:25px;top:376px;width:234px;height:220px;border-radius:10px;background:linear-gradient(135deg,#dfe3e8,#6d7a8c)}
.front-copy{position:absolute;left:26px;right:26px;text-align:center}
.front-copy h2{font-family:'Montserrat',sans-serif;font-weight:700;font-size:12.6px;letter-spacing:.2px;color:var(--ink)}
.front-copy p{font-size:5.6px;line-height:12.1px;color:var(--body);font-weight:300;margin-top:4px}
.front-copy--intro{top:342px}
.front-copy--grow{top:415px}
.front-copy--grow h2{margin-bottom:3px}
.front-copy--grow p{margin-top:2px}
.section-title{position:absolute;font-family:'Montserrat',sans-serif;font-weight:700;font-size:12.4px;color:var(--ink)}
.section-title .accent{color:var(--sky)}
.section-title--expertise{left:24px;top:55px}
.section-title--why{left:280px;top:378px;font-size:12.6px}
.expertise{position:absolute;left:25px;top:86px;width:470px;list-style:none}
.expertise li{position:relative;height:52px;padding-left:55px}
.expertise__icon{position:absolute;left:0;top:0;width:44px;height:42px;background:var(--navy);border-radius:5px;display:flex;align-items:center;justify-content:center}
.expertise h3{font-weight:400;font-size:10px;line-height:13px;padding-top:1px}
.expertise p{font-size:5.9px;line-height:12px;color:var(--body);font-weight:300;margin-top:2px}
.reasons{position:absolute;left:280px;top:404px;width:220px}
.reasons h3{font-weight:400;font-size:10px;line-height:13px}
.reasons p{font-size:5.9px;line-height:12px;color:var(--body);font-weight:300;margin:3px 0 5px}
.contact-bar{position:absolute;left:0;bottom:0;width:518px;height:36px;background:var(--sky);color:#fff}
.contact{position:absolute;top:9px;display:flex;gap:8px;align-items:flex-start}
.contact--phone{left:25px}
.contact--email{left:178px}
.contact--location{left:329px}
.contact strong{display:block;font-weight:600;font-size:7px;line-height:9px}
.contact span{display:block;font-size:6.8px;line-height:10px}
</style>
</head>
<body>
<main class="stage">
  <svg class="backdrop" width="1200" height="793" viewBox="0 0 1200 793" aria-hidden="true">
    <rect width="1200" height="793" fill="var(--backdrop)"/>
    <path d="M0 395 C200 320 420 305 560 300 L1200 300 L1200 793 L0 793 Z" fill="var(--navy)"/>
    <circle cx="1088" cy="-38" r="55" fill="#fff"/>
    <circle cx="132" cy="830" r="58" fill="#fff"/>
  </svg>

  <section class="page page--front">
    <div class="firm-name">Vennory Law</div>
    <div class="photo photo--team" role="img" aria-label="Photo of four smiling professionals in business attire standing with arms crossed in a city street"></div>

    <div class="front-copy front-copy--intro">
      <h2>YOUR TRUSTED PARTNER IN HEALTHCARE LAW</h2>
      <p>At Vennory Law, our dedicated Healthcare Law Practice Group is committed to safeguarding the interests of healthcare businesses like yours.<br>Our team understands the unique challenges of this highly regulated industry. We are experienced in navigating the complexities of healthcare law to protect<br>your business, allowing you to focus on what you do best: delivering exceptional care.</p>
    </div>

    <div class="front-copy front-copy--grow">
      <h2>PROTECTING &amp; HELPING YOUR BUSINESS GROW</h2>
      <p>Whether you're starting a new business or managing an established enterprise, the focus of your attention and energy is on developing and commercializing your practice, products, and/or services. Due to time constraints and the overwhelming amount of work your business requires, proper legal planning sometimes takes a back seat. We can help. Vennory Law seeks to relieve the stress and anxiety associated with unaddressed legal issues by handling these challenges and allowing our clients to focus on growing their companies.</p>
      <p>Our Healthcare Law practice encompasses a wide range of services. We guide clients through the proper establishment of new businesses, and the myriad issues that arise as companies interact with the public, other companies, regulatory bodies, and the government. We help make sure businesses are correctly organized and comply with state and federal laws, rules, and regulations pertaining to raising capital, acquiring other businesses or assets, protecting patient information, complying with health law regulations and statutes, and adding and removing owners.</p>
      <p>Buying a healthcare business, cementing a strategic partnership, and executing an exit event are all fraught with pitfalls and unexpected risks. When a deal or contract needs to get negotiated, documented, and closed - we excel. We fight to get the right deal terms for our clients and offer creative solutions to help navigate these minefields and achieve a successful result.</p>
      <p>We work with all forms of businesses including partnerships, limited liability companies (LLCs), and corporations. Regardless of the type of business,<br>it is imperative that the potential legal threats and obstacles the business may face are properly addressed.</p>
    </div>
  </section>

  <section class="page page--back">
    <div class="firm-name">Vennory Law</div>

    <h2 class="section-title section-title--expertise">EXAMPLES OF OUR <span class="accent">EXPERTISE</span></h2>
    <ul class="expertise">
      <li>
        <div class="expertise__icon"><svg width="26" height="26" viewBox="0 0 26 26" fill="none" stroke="#fff" stroke-width="1.2"><path d="M12 2 L21 5 V12 C21 18 17 22 12 24 C7 22 3 18 3 12 V5 Z"/><path d="M12 8 V16 M8 12 H16"/><circle cx="20" cy="20" r="3"/></svg></div>
        <h3>Medical Practices</h3>
        <p>Navigating the intricate landscape of healthcare regulations, regulatory compliance, and business legal issues. We ensure that your practice operates smoothly while avoiding costly legal pitfalls.</p>
      </li>
      <li>
        <div class="expertise__icon"><svg width="26" height="26" viewBox="0 0 26 26" fill="none" stroke="#fff" stroke-width="1.2"><rect x="7" y="3" width="11" height="4" rx="1"/><rect x="5" y="7" width="15" height="16" rx="2"/><path d="M12.5 11 V19 M8.5 15 H16.5"/><circle cx="21" cy="21" r="2.5"/></svg></div>
        <h3>Med Spas</h3>
        <p>Guiding med spas through confusing and ever-changing regulations, licensing, and compliance issues while ensuring their operations are legally sound.</p>
      </li>
      <li>
        <div class="expertise__icon"><svg width="26" height="26" viewBox="0 0 26 26" fill="none" stroke="#fff" stroke-width="1.2"><path d="M3 11 L13 5 L23 11 V23 H3 Z"/><path d="M13 1 V7 M10 4 H16"/><rect x="6" y="13" width="3" height="3"/><rect x="11.5" y="13" width="3" height="3"/><rect x="17" y="13" width="3" height="3"/><rect x="6" y="18" width="3" height="3"/><rect x="17" y="18" width="3" height="3"/><path d="M11.5 23 V18 H14.5 V23"/></svg></div>
        <h3>Medical Device Companies</h3>
        <p>Providing counsel on regulatory compliance, intellectual property, product liability, and contracts to help device manufacturers succeed in a competitive marketplace.</p>
      </li>
      <li>
        <div class="expertise__icon"><svg width="26" height="26" viewBox="0 0 26 26" fill="none" stroke="#fff" stroke-width="1.2"><rect x="2" y="7" width="18" height="12" rx="1"/><path d="M8 23 H14 M11 19 V23"/><rect x="18" y="4" width="6" height="16" rx="1"/><circle cx="8" cy="6" r="4"/><path d="M8 4 V8 M6 6 H10"/></svg></div>
        <h3>Medical Software Companies</h3>
        <p>Addressing the unique legal needs of software companies in healthcare, including data privacy, cybersecurity, and regulatory compliance.</p>
      </li>
      <li>
        <div class="expertise__icon"><svg width="26" height="26" viewBox="0 0 26 26" fill="none" stroke="#fff" stroke-width="1.2"><circle cx="13" cy="13" r="6"/><path d="M13 10 V16 M10 13 H16"/><path d="M3 18 C6 22 10 24 15 23 L20 20"/><path d="M23 8 C20 4 16 2 11 3 L6 6"/></svg></div>
        <h3>Weight Loss and Pain Management Clinics</h3>
        <p>Offering guidance and support on compliance, licensing, and patient care and safety to ensure exceptional care while adhering to strict regulatory standards.</p>
      </li>
    </ul>

    <div class="photo photo--staff" role="img" aria-label="Photo of a smiling team of five professionals standing together in a bright office"></div>

    <h2 class="section-title section-title--why"><span class="accent">WHY</span> CHOOSE VENNORY LAW?</h2>
    <div class="reasons">
      <h3>Industry-Focused</h3>
      <p>Our deep understanding of the healthcare sector enables us to provide tailored legal solutions.</p>
      <h3>Experienced Team</h3>
      <p>Our HIPAA certified attorneys have extensive experience in healthcare law, delivering effective counsel and representation.</p>
      <h3>Proactive Approach</h3>
      <p>We anticipate challenges before they arise, providing strategic advice to safeguard your business.</p>
      <h3>Comprehensive Services</h3>
      <p>From compliance to drafting legal documents to dispute resolution, we offer end-to-end legal support for most healthcare law needs.</p>
    </div>

    <footer class="contact-bar">
      <div class="contact contact--phone">
        <svg width="18" height="18" viewBox="0 0 24 24" fill="none" stroke="#fff" stroke-width="1.6"><path d="M5 3 L9 3 L10.5 8 L8 9.5 C9 12 12 15 14.5 16 L16 13.5 L21 15 V19 C21 20 20 21 19 21 C10 21 3 14 3 5 C3 4 4 3 5 3 Z"/><path d="M15 3 C18 4 20 6 21 9 M15 6.5 C16.5 7 17.5 8 18 9.5"/></svg>
        <div><strong>Phone:</strong><span>555-014-2290</span></div>
      </div>
      <div class="contact contact--email">
        <svg width="18" height="18" viewBox="0 0 24 24" fill="none" stroke="#fff" stroke-width="1.6"><rect x="2" y="5" width="20" height="14"/><path d="M2 5 L12 13 L22 5 M2 19 L9 11 M22 19 L15 11"/></svg>
        <div><strong>Email:</strong><span>info@vennory.law</span></div>
      </div>
      <div class="contact contact--location">
        <svg width="18" height="18" viewBox="0 0 24 24" fill="none" stroke="#fff" stroke-width="1.6"><path d="M12 21 C12 21 5 13.5 5 9 A7 7 0 0 1 19 9 C19 13.5 12 21 12 21 Z"/><circle cx="12" cy="9" r="2.5"/><path d="M6 22 H18"/></svg>
        <div><strong>Location:</strong><span>48 Harbor Crest Lane, Seaview, C.A. 90000</span></div>
      </div>
    </footer>
  </section>
</main>
</body>
</html>
```